4th Generation Family Business Needs a New Card Design!

We are a family owned 4th Generation company. We are based in the Sydney, Australia area and we are desperately in need of a more modern and classy card. We are monumental masons who design, supply & erect lasting memorials throughout cemeteries in Sydney. Our customers are normally in a period of grieving. I have attached logo files that will need to be implemented on the card. Company was established 1935. Australian Owned and Operated. Card needs to be designed to PIXO.com specification.

Target Market(s)

Our target market is based upon people that a grieving for family members that have passed away. We also deal with alot of companies that own and operate cemeteries.

Industry/Entity Type

Business

Contact Information for Business Card

Simon Harcourt, Operations Manager, 0417293086, simon@harcourtmemorials.com.au
Lewis Harcourt, Director, 0491630572, lewis@harcourtmemorials.com.au
Phone # 02 9561 3048
Website: www.harcourtmemorials.com.au
Address: Suite 17, 8 Palfrey Lane, West Carlow, Sydney NSW 2156

Font styles to use
Serif
Decorative
Script

Requirements
Must have
• Would like to see the logo nicely implemented with a modern design. Embossed lettering would be a nice additive.

```html
<!DOCTYPE html>
<html lang="en">
<head>
<meta charset="utf-8">
<title>Harcourt Memorials – Business Card</title>
<link rel="stylesheet" href="https://fonts.googleapis.com/css2?family=Arimo:wght@400;700&display=swap">
<style>
  :root {
    --bg: #e9e6e1;
    --card-white: #ffffff;
    --card-black: #222222;
    --gold: #f0be2a;
    --ink: #2a2a2a;
    --grey: #666666;
    --light: #ffffff;
  }
  * { box-sizing: border-box; margin: 0; padding: 0; }
  html, body { width: 1200px; height: 950px; overflow: hidden; }
  body {
    background: var(--bg);
    position: relative;
    font-family: "Arimo", Arial, sans-serif;
  }
  .card {
    position: absolute;
    box-shadow: 0 6px 18px rgba(0,0,0,0.18);
  }

  /* Front (portrait) */
  .card-front {
    left: 50px; top: 145px;
    width: 400px; height: 660px;
    background: var(--card-white);
    color: var(--ink);
  }
  .name-band {
    position: absolute;
    top: 42px; right: 0;
    width: 300px; height: 100px;
    background: var(--gold);
    clip-path: polygon(0 0, 100% 0, 100% 100%, 12% 100%, 0 70%);
    padding: 18px 0 0 28px;
  }
  .person-name { font-weight: 700; font-size: 20px; line-height: 1.2; color: var(--ink); }
  .person-title { font-size: 16px; line-height: 1.2; color: var(--ink); margin-top: 6px; }

  .wordmark {
    position: absolute;
    left: 0; right: 0;
    display: flex; align-items: center; justify-content: center; gap: 12px;
    font-family: "Arimo", Arial, sans-serif;
    font-weight: 400;
    line-height: 1;
    white-space: nowrap;
  }
  .wordmark-square { width: 16px; height: 16px; background: var(--gold); flex: none; }
  .card-front .wordmark { top: 245px; color: var(--ink); font-size: 28px; }

  .contact {
    position: absolute;
    right: 34px;
    text-align: right;
    font-size: 15px;
    color: var(--grey);
    line-height: 1.6;
  }
  .address { top: 390px; }
  .numbers { top: 470px; }
  .numbers b { color: var(--ink); }

  /* Back (landscape) */
  .card-back {
    left: 500px; top: 278px;
    width: 650px; height: 394px;
    background: var(--card-black);
  }
  .card-back .wordmark {
    top: 50%; transform: translateY(-50%);
    color: var(--light); font-size: 36px;
  }
  .card-back .wordmark-square { width: 20px; height: 20px; }
</style>
</head>
<body>
  <section class="card card-front" aria-label="Business card front">
    <div class="name-band">
      <p class="person-name">Simon Harcourt</p>
      <p class="person-title">Operations Manager</p>
    </div>

    <div class="wordmark">
      <span class="wordmark-square"></span>
      <span class="wordmark-name">Harcourt Memorials</span>
    </div>

    <p class="contact address">Suite 17, 8 Palfrey Lane<br>West Carlow, Sydney NSW 2156</p>
    <p class="contact numbers">
      <b>P :</b> 02 9561 3048<br>
      <b>M :</b> 0417293086<br>
      simon@harcourtmemorials.com.au<br>
      www.harcourtmemorials.com.au
    </p>
  </section>

  <section class="card card-back" aria-label="Business card back">
    <div class="wordmark">
      <span class="wordmark-square"></span>
      <span class="wordmark-name">Harcourt Memorials</span>
    </div>
  </section>
</body>
</html>
```